Business card design for sustainable building and development company

Need a business card design for a new sustainable building and real estate development company in the San Francisco Bay area. Name of company is "Tovrin Advisors, LLC" and we provide "Sustainable building, energy and development services" for residential and non residential projects. We'd like the following colors used but not all area required: green, gray, blue. Design should communicate innovation, professionalism and sustainability. Our current website is www.tovrin-advisors.example. Another possible design idea is to have the following listed on the back of the card:
Certified: VERN QS, Eco Marker Rater, DOLM Rater, Terravue Inspector, KSO TQ Building Analyst. Its not a must but could be text that could be used for back of card. Overall, we are open to a simple, clean design and or one with more text than usual for a card.

Industry/Entity Type

Real Estate

Contact Information for Business Card

Name on card: Mark J. Halvik
Title for Name: Principal + Founder
Phone: 555.814.0627
Email: mhalvik@tovrin-advisors.example
Website: www.tovrin-advisors.example

Also, please add the following for address:
San Francisco, California

Requirements
Nice to have
• If you can integrate the outline of a skyline on the backside of the card and if it looks good, I would like to see the design
Should not have
• a barcode;

```html
<!DOCTYPE html>
<html lang="en">
<head>
<meta charset="utf-8">
<title>Tovrin Advisors – Business Card</title>
<link rel="stylesheet" href="https://fonts.googleapis.com/css2?family=Montserrat:wght@600&family=Exo+2:wght@400;500&display=swap">
<style>
  :root{
    --green:#6abf4b;
    --green-soft:#a9da93;
    --ink:#1e1e1e;
    --paper:#ffffff;
    --paper-shade:#ececec;
    --backdrop:#e9e6e1;
    --type-white:#ffffff;
  }
  *{margin:0;padding:0;box-sizing:border-box}
  html,body{width:1200px;height:899px;overflow:hidden;background:var(--backdrop)}
  .canvas{position:relative;width:1200px;height:899px}
  .card{
    position:absolute;left:250px;width:700px;height:400px;
    background:linear-gradient(120deg,var(--paper) 40%,var(--paper-shade));
    box-shadow:0 6px 18px rgba(0,0,0,.18);overflow:hidden;
  }
  .card-back{top:28px}
  .card-front{top:471px}
  .card-shapes{position:absolute;inset:0;width:100%;height:100%}
  .back-website{
    position:absolute;left:34px;top:235px;color:var(--type-white);
    font:500 15px/1 "Exo 2",sans-serif;letter-spacing:.5px;
  }
  .building-art{position:absolute;left:430px;top:22px;width:240px;height:270px}
  .brand{position:absolute;left:40px;top:115px;width:300px;text-align:center}
  .brand-mark{width:62px;height:62px;border:6px solid var(--green);border-radius:50%;margin:0 auto 12px}
  .brand-name{font:600 33px/1 "Montserrat",sans-serif;color:var(--green);letter-spacing:-.5px;white-space:nowrap}
  .brand-tagline{margin-top:6px;font:600 8.6px/1 "Montserrat",sans-serif;color:var(--ink);letter-spacing:.2px;white-space:nowrap}
  .contact{
    position:absolute;right:36px;top:40px;text-align:right;color:var(--type-white);
    font-family:"Exo 2",sans-serif;
  }
  .person-name{font-size:20px;font-weight:500;letter-spacing:1.5px}
  .person-title{font-size:14px;margin-top:3px}
  .address{font-size:14px;line-height:1.5;margin-top:40px}
  .contact-list{list-style:none;margin-top:30px;font-size:13px}
  .contact-list li{display:flex;justify-content:flex-end;align-items:center;gap:8px;height:24px;white-space:nowrap}
  .contact-list svg{width:14px;height:14px;flex:none;fill:none;stroke:var(--type-white);stroke-width:1.6}
</style>
</head>
<body>
<main class="canvas">

  <section class="card card-back" aria-label="Card back">
    <svg class="card-shapes" viewBox="0 0 700 400" preserveAspectRatio="none">
      <polygon fill="var(--ink)" points="236,0 256,0 326,198 250,400 238,400 306,200"/>
      <polygon fill="var(--green)" points="0,0 236,0 306,200 238,400 0,400"/>
    </svg>
    <p class="back-website">www.yoursite.example</p>
    <svg class="building-art" role="img" aria-label="Green outline illustration of a tall office building seen from below" viewBox="0 0 240 270">
      <defs>
        <linearGradient id="buildingTone" x1="0" y1="0" x2="1" y2="1">
          <stop offset="0" stop-color="var(--green)"/>
          <stop offset="1" stop-color="var(--green-soft)"/>
        </linearGradient>
      </defs>
      <polygon fill="url(#buildingTone)" points="40,60 120,0 240,110 240,240 70,270"/>
    </svg>
  </section>

  <section class="card card-front" aria-label="Card front">
    <svg class="card-shapes" viewBox="0 0 700 400" preserveAspectRatio="none">
      <polygon fill="var(--ink)" points="296,0 318,0 452,215 418,400 404,400 430,222"/>
      <polygon fill="var(--green)" points="318,0 700,0 700,400 418,400 452,215"/>
    </svg>

    <div class="brand">
      <div class="brand-mark"></div>
      <p class="brand-name">Tovrin Advisors</p>
      <p class="brand-tagline">RESPONSIBLE DESIGN, POWER &amp; PROPERTY ADVISORY WORK</p>
    </div>

    <div class="contact">
      <p class="person-name">ELIN VARROW</p>
      <p class="person-title">Managing Director</p>
      <p class="address">041.9th floor.Quay<br>Harbor Road TKM</p>
      <ul class="contact-list">
        <li>012 555 0148
          <svg viewBox="0 0 16 16"><path d="M3 2l3 0 1 4-2 1c1 2 2 3 4 4l1-2 4 1 0 3c-6 1-12-5-11-11z"/></svg></li>
        <li>012 555 0148
          <svg viewBox="0 0 16 16"><rect x="4.5" y="1.5" width="7" height="13" rx="1"/><line x1="7" y1="12" x2="9" y2="12"/></svg></li>
        <li>012 555 0148
          <svg viewBox="0 0 16 16"><rect x="2" y="6" width="12" height="8" rx="1"/><rect x="5" y="2" width="6" height="4"/></svg></li>
        <li>yourname@mail.example
          <svg viewBox="0 0 16 16"><rect x="1.5" y="3.5" width="13" height="9"/><path d="M1.5 3.5l6.5 5 6.5-5"/></svg></li>
        <li>www.yoursite.example
          <svg viewBox="0 0 16 16"><circle cx="8" cy="8" r="6.5"/><ellipse cx="8" cy="8" rx="3" ry="6.5"/><line x1="1.5" y1="8" x2="14.5" y2="8"/></svg></li>
      </ul>
    </div>
  </section>

</main>
</body>
</html>
```